We are a recruitment company based in Norwich/Cambridge England.
I have included our company logo which we want to remain the same.

What we are looking for is a new creative Business card which will really stand out!!

Contact Information for Business Card

Harriet Dunmore
email: Harriet@plavex.co.uk
Address: Brackwell House
Fenmoor Enterprise Park
Partridge Way
Norwich
QB9 3KX
Tel:01632 960418

```html
<!DOCTYPE html>
<html lang="en">
<head>
<meta charset="utf-8">
<title>Plavex Business Card</title>
<link rel="stylesheet" href="https://fonts.googleapis.com/css2?family=Roboto:wght@400;500&family=Roboto+Condensed:wght@500&display=swap">
<style>
  :root {
    --backdrop: #2b2b2b;
    --brand-green: #8dc63f;
    --brand-grey: #8c878d;
    --card-back: #8e898f;
    --paper: #f2f2f2;
    --ink-light: #ffffff;
  }
  html, body {
    margin: 0;
    padding: 0;
    width: 1200px;
    height: 960px;
    overflow: hidden;
    background: var(--backdrop);
  }
  .canvas {
    position: relative;
    width: 1200px;
    height: 960px;
  }
  .card {
    position: absolute;
    width: 600px;
    height: 342px;
    overflow: hidden;
  }
  .card--front { left: 322px; top: 108px; background: var(--brand-green); }
  .card--back { left: 320px; top: 493px; background: var(--card-back); }

  .front-shape { position: absolute; inset: 0; }

  .contact {
    position: absolute;
    left: 33px;
    top: 26px;
    color: var(--ink-light);
    font-family: "Roboto", Arial, sans-serif;
  }
  .contact__name {
    margin: 0;
    font-family: "Roboto Condensed", "Arial Narrow", sans-serif;
    font-weight: 500;
    font-size: 22px;
    line-height: 26px;
    text-transform: uppercase;
  }
  .contact__role {
    margin: 0 0 14px;
    font-size: 16px;
    line-height: 20px;
    text-transform: uppercase;
  }
  .contact__address {
    margin: 0 0 10px;
    font-style: normal;
    font-size: 15px;
    line-height: 19px;
  }
  .contact__list {
    list-style: none;
    margin: 0;
    padding: 0;
    font-size: 15px;
    line-height: 19.5px;
  }
  .contact__list li { display: flex; align-items: center; gap: 8px; }
  .contact__icon { width: 14px; height: 14px; flex: none; }

  .brand {
    position: absolute;
    left: 272px;
    top: 232px;
    display: flex;
    align-items: center;
    gap: 14px;
  }
  .brand__dot {
    width: 58px;
    height: 58px;
    border-radius: 50%;
    background: var(--brand-green);
  }
  .brand__text { display: flex; flex-direction: column; }
  .brand__name {
    font-family: "Roboto", Arial, sans-serif;
    font-weight: 500;
    font-size: 46px;
    line-height: 48px;
    color: var(--brand-grey);
  }
  .brand__tagline {
    font-family: "Roboto", Arial, sans-serif;
    font-size: 9px;
    letter-spacing: 1.6px;
    color: var(--brand-grey);
  }

  .back-mark {
    position: absolute;
    left: 0;
    right: 0;
    top: 120px;
    text-align: center;
    font-family: "Roboto", Arial, sans-serif;
    font-weight: 500;
    font-size: 72px;
    line-height: 80px;
    color: var(--ink-light);
  }
  .back-web {
    position: absolute;
    left: 0;
    right: 0;
    top: 298px;
    text-align: center;
    font-family: "Roboto", Arial, sans-serif;
    font-size: 14px;
    letter-spacing: 6px;
    color: var(--ink-light);
  }
</style>
</head>
<body>
<main class="canvas">
  <section class="card card--front" aria-label="Business card front">
    <svg class="front-shape" width="600" height="342" viewBox="0 0 600 342" aria-hidden="true">
      <path d="M499,0 C414,10 339,60 336,163 C244,163 154,200 137,342 L600,342 L600,0 Z" fill="var(--brand-grey)"/>
      <path d="M507,0 C422,10 346,60 343,170 C252,170 162,205 145,342 L600,342 L600,0 Z" fill="var(--paper)"/>
    </svg>

    <div class="contact">
      <h1 class="contact__name">Harriet Dunmore</h1>
      <p class="contact__role">Director</p>
      <address class="contact__address">Brackwell House<br>Norwich QB9 3KX</address>
      <ul class="contact__list">
        <li>
          <svg class="contact__icon" viewBox="0 0 24 24" aria-hidden="true"><path fill="#fff" d="M6.6 10.8a15.1 15.1 0 0 0 6.6 6.6l2.2-2.2a1 1 0 0 1 1-.25 11.4 11.4 0 0 0 3.6.57 1 1 0 0 1 1 1V20a1 1 0 0 1-1 1A17 17 0 0 1 3 4a1 1 0 0 1 1-1h3.5a1 1 0 0 1 1 1c0 1.25.2 2.45.57 3.57a1 1 0 0 1-.25 1z"/></svg>
          01632 960418
        </li>
        <li>
          <svg class="contact__icon" viewBox="0 0 24 24" aria-hidden="true"><path fill="#fff" d="M3 6h18v12H3z"/><path fill="none" stroke="var(--brand-green)" stroke-width="1.8" d="M3 6l9 7 9-7"/></svg>
          Harriet@plavex.co.uk
        </li>
        <li>
          <svg class="contact__icon" viewBox="0 0 24 24" aria-hidden="true"><circle cx="12" cy="12" r="10" fill="#fff"/><path fill="none" stroke="var(--brand-green)" stroke-width="1.6" d="M2 12h20M12 2c3 3 3 17 0 20M12 2c-3 3-3 17 0 20"/></svg>
          www.plavex.co.uk
        </li>
      </ul>
    </div>

    <div class="brand">
      <span class="brand__dot" aria-hidden="true"></span>
      <div class="brand__text">
        <span class="brand__name">Plavex</span>
        <span class="brand__tagline">Technology Recruitment</span>
      </div>
    </div>
  </section>

  <section class="card card--back" aria-label="Business card back">
    <div class="back-mark">Plavex</div>
    <div class="back-web">www.plavex.co.uk</div>
  </section>
</main>
</body>
</html>
```